Communication and Marketing agency needs a new presentation card

We are a group of communication and marketing agencies specialized in companies that are in the logistics and industrial sector. The head agency is TELVANO Grupo and the group consists of 4 agencies: TELVANO Media, TELVANO Digital, TELVANO Research and DifundeEnPantalla. We hace 4 offices in Spain (Madrid, Barcelona, Valencia and Murcia). We are looking for a clean and attractive design that transmits our experience, brand presence in the market and knowledge to those who receive the card.It has to maintain the colors of the logo that is attached.
Target Market(s)
logistics and industrial sector
Marketing department
Contact Information for Business Card
Clean and attractive design

```html
<!DOCTYPE html>
<html lang="en">
<head>
<meta charset="utf-8">
<title>TELVANO Business Card</title>
<link rel="stylesheet" href="https://fonts.googleapis.com/css2?family=Open+Sans:wght@400;600;700&display=swap">
<style>
  :root {
    --stage: #a81f25;
    --card-dark: #1c1c1c;
    --map-tone: #262626;
    --card-light: #f7f7f7;
    --brand-red: #b01d27;
    --brand-grey: #5e5e5e;
    --ink: #222222;
    --swoosh: #4a4a4a;
  }
  * { margin: 0; padding: 0; box-sizing: border-box; }
  html, body { width: 1200px; height: 1200px; overflow: hidden; }
  body {
    background: var(--stage);
    font-family: "Open Sans", Arial, sans-serif;
    position: relative;
  }
  .card {
    position: absolute;
    left: 224px;
    width: 814px;
    height: 465px;
    overflow: hidden;
  }
  .card--front { top: 76px; background: var(--card-dark); }
  .card--back { top: 658px; background: var(--card-light); }

  .world-map {
    position: absolute;
    inset: 20px 0 40px 0;
    background: radial-gradient(ellipse at 55% 45%, var(--map-tone) 0%, var(--map-tone) 45%, rgba(28,28,28,0) 75%);
  }
  .front-brand {
    position: absolute;
    left: 120px;
    width: 543px;
    top: 132px;
    text-align: right;
    color: var(--brand-grey);
    font-weight: 400;
    line-height: 1;
    white-space: nowrap;
  }
  .front-brand__name { display: block; font-size: 106px; letter-spacing: 1px; }
  .front-brand__unit { display: block; font-size: 62px; margin-top: 10px; }

  .back-brand {
    position: absolute;
    left: 30px;
    width: 352px;
    top: 160px;
    color: var(--brand-red);
    font-weight: 400;
    text-align: right;
    line-height: 1;
    white-space: nowrap;
  }
  .back-brand__name { display: block; font-size: 68px; }
  .back-brand__unit { display: block; font-size: 38px; margin-top: 8px; }

  .divider {
    position: absolute;
    left: 415px;
    top: 138px;
    width: 2px;
    height: 182px;
    background: var(--brand-red);
  }
  .contact {
    position: absolute;
    left: 452px;
    top: 134px;
    color: var(--ink);
    white-space: nowrap;
  }
  .contact__name { font-size: 32px; font-weight: 700; line-height: 1.1; }
  .contact__role { font-size: 18px; color: var(--brand-red); line-height: 1.3; }
  .contact__address { font-size: 18px; line-height: 1.35; }
  .contact__list { list-style: none; margin-top: 8px; font-size: 18px; line-height: 1.3; }
  .contact__list li { display: flex; align-items: center; gap: 9px; }
  .contact__list svg { width: 13px; height: 13px; flex: none; }

  .wave { position: absolute; left: 0; bottom: 0; width: 814px; height: 465px; }
</style>
</head>
<body>

  <section class="card card--front">
    <div class="world-map" role="img" aria-label="Faint dotted world map spread across the card"></div>
    <div class="front-brand">
      <span class="front-brand__name">TELVANO</span>
      <span class="front-brand__unit">Digital</span>
    </div>
  </section>

  <section class="card card--back">
    <div class="back-brand">
      <span class="back-brand__name">TELVANO</span>
      <span class="back-brand__unit">Grupo</span>
    </div>
    <div class="divider"></div>
    <div class="contact">
      <p class="contact__name">Marco Ellison</p>
      <p class="contact__role">Manager</p>
      <p class="contact__address">#118 – 4470 Ridgeway Road NW<br>Lakeview AB T4K 2P7 CANADA</p>
      <ul class="contact__list">
        <li>
          <svg viewBox="0 0 14 14"><path d="M3 1h3l1 3-2 1.5c.8 1.6 2 2.8 3.5 3.5L10 7l3 1v3c0 1-1 2-2 2C6 13 1 8 1 3c0-1 1-2 2-2z" fill="var(--brand-red)"/></svg>
          +587 -555- 0142
        </li>
        <li>
          <svg viewBox="0 0 14 14"><rect x="0.5" y="2.5" width="13" height="9" fill="var(--brand-red)"/><path d="M1 3l6 5 6-5" stroke="#fff" stroke-width="1.2" fill="none"/></svg>
          info@brightlane.ca
        </li>
        <li>
          <svg viewBox="0 0 14 14"><circle cx="7" cy="7" r="6" fill="none" stroke="var(--brand-red)" stroke-width="1.3"/><path d="M1 7h12M7 1v12M3 3.5c2.5 1.5 5.5 1.5 8 0M3 10.5c2.5-1.5 5.5-1.5 8 0" stroke="var(--brand-red)" stroke-width="1" fill="none"/></svg>
          www.brightlane.ca
        </li>
      </ul>
    </div>
    <svg class="wave" viewBox="0 0 814 465" aria-hidden="true">
      <path d="M0 418 C250 450 560 448 814 382 L814 465 L0 465 Z" fill="var(--brand-red)"/>
      <path d="M0 401 C150 422 320 438 452 441 C320 444 150 430 0 412 Z" fill="var(--swoosh)"/>
    </svg>
  </section>

</body>
</html>
```